Sparrow Haulage needs a business card design.

Design a double-sided business card for new freight business. On the front, would like to see our logo along with the following info:

Martin Obuya
CEO/FOUNDER
555-206-7142
martinobuya@sparrow-haulage.example

On the reverse side, we would like to use the graphic image of our logo only without the Sparrow Haulage name.

```html
<!DOCTYPE html>
<html lang="en">
<head>
<meta charset="utf-8">
<title>Sparrow Haulage — Business Card</title>
<link rel="stylesheet" href="https://fonts.googleapis.com/css2?family=Open+Sans:wght@400;600;700&display=swap">
<style>
  :root {
    --navy: #1b1a5c;
    --navy-deep: #14134a;
    --navy-light: #2c3386;
    --red: #b81f2a;
    --white: #ffffff;
    --backdrop: #c4c4c4;
  }
  * { box-sizing: border-box; margin: 0; padding: 0; }
  html, body { width: 1200px; height: 788px; overflow: hidden; }
  body {
    background: var(--backdrop);
    font-family: "Open Sans", Arial, sans-serif;
    display: flex;
    align-items: center;
    justify-content: center;
    gap: 40px;
  }
  .card {
    position: relative;
    width: 540px;
    height: 309px;
    border-radius: 22px;
    overflow: hidden;
    box-shadow: 0 10px 24px rgba(0,0,0,0.28);
  }
  .card-front { background: var(--white); }
  .front-wave { position: absolute; inset: 0; width: 100%; height: 100%; }
  .brand-name {
    position: absolute;
    left: 34px;
    top: 118px;
    color: var(--navy);
    font-weight: 700;
    font-size: 25px;
    line-height: 1.1;
    letter-spacing: 3px;
    text-transform: uppercase;
  }
  .contact {
    position: absolute;
    right: 26px;
    top: 50px;
    text-align: right;
    color: var(--white);
  }
  .contact-name { font-size: 22px; font-weight: 700; line-height: 1.3; }
  .contact-title { font-size: 13px; font-weight: 400; letter-spacing: 0.5px; margin-bottom: 14px; }
  .contact-line {
    display: flex;
    justify-content: flex-end;
    align-items: center;
    gap: 7px;
    font-size: 12px;
    line-height: 1.8;
    white-space: nowrap;
  }
  .contact-line svg { width: 11px; height: 11px; flex: none; }
  .card-back { background: var(--navy); }
  .back-pattern {
    position: absolute;
    inset: 0;
    background: linear-gradient(135deg, var(--navy-deep) 0%, var(--navy) 55%, var(--navy-light) 100%);
  }
</style>
</head>
<body>
  <section class="card card-front" aria-label="Business card front">
    <svg class="front-wave" viewBox="0 0 540 309" preserveAspectRatio="none" aria-hidden="true">
      <path d="M330,0 C270,40 258,150 216,230 C190,280 158,300 134,309 L540,309 L540,0 Z" fill="#1b1a5c"/>
      <path d="M314,0 C254,40 242,150 200,230 C174,280 142,300 118,309" fill="none" stroke="#b81f2a" stroke-width="6"/>
      <path d="M323,0 C263,40 251,150 209,230 C183,280 151,300 127,309" fill="none" stroke="#b81f2a" stroke-width="2"/>
    </svg>
    <div class="brand-name">Sparrow<br>Haulage</div>
    <div class="contact">
      <p class="contact-name">Martin Obuya</p>
      <p class="contact-title">CEO/FOUNDER</p>
      <p class="contact-line">555-206-7142
        <svg viewBox="0 0 12 12"><path d="M3 1l2 2-1 1.5c.6 1.4 1.6 2.4 3 3L8.5 6.5l2 2L9 10.5C5 10 2 7 1.5 3z" fill="#fff"/></svg>
      </p>
      <p class="contact-line">martinobuya@sparrow-haulage.example
        <svg viewBox="0 0 12 12"><rect x="1" y="2.5" width="10" height="7" fill="#fff"/><path d="M1 2.5l5 4 5-4" fill="none" stroke="#1b1a5c" stroke-width="1"/></svg>
      </p>
      <p class="contact-line">www.sparrow-haulage.example
        <svg viewBox="0 0 12 12"><circle cx="6" cy="6" r="5" fill="#fff"/><path d="M1 6h10M6 1c-2 2.5-2 7.5 0 10M6 1c2 2.5 2 7.5 0 10" fill="none" stroke="#1b1a5c" stroke-width="0.8"/></svg>
      </p>
    </div>
  </section>

  <section class="card card-back" aria-label="Business card back">
    <div class="back-pattern" role="img" aria-label="Repeating pattern of the company mark in tones of navy and blue"></div>
  </section>
</body>
</html>
```